Elegant, Playful ReDesign of Paperlynx Website in wordpress - Budget has been raised

Project Brief: Paperlynx Website Redesign in WordPress

Introduction: Paperlynx, a cutting-edge document creation solution, aims to revolutionize the tedious process of crafting contracts, offers, forms, and other documents. By saving customers valuable time, streamlining workflows, and minimizing human error, Paperlynx has become an essential tool. As a technology company with a diverse clientele, we're set to boost our online presence through a refreshed WordPress website. Beyond a modernized website, we aspire to establish a stronger brand identity, incorporating graphic elements seamlessly into our online presence.

Current Status: Currently hosted on WordPress, Paperlynx's existing website serves its purpose but is ready for a visual transformation. Our goal is to maintain a modern and attractive appearance while upholding our commitment to simplicity and efficiency. Notably, the website is currently only in Danish. The redesigned structure should include a language switch function to cater to future international customers.

Objectives:
• Modern Aesthetic: Redesign the website with a fresh and modern vibe, reflecting innovation in the document creation sphere.
• User-Friendly: Prioritize an intuitive design for seamless navigation, ensuring visitors easily understand our offerings and benefits.
• Informative Content: Strike a balance between attractiveness and informativeness, clearly communicating Paperlynx's value proposition and simplifying business processes.
• Graphic Elements: Integrate visually appealing graphics that enhance the site's aesthetics and contribute to our overall visual identity. These elements should be versatile for future use in social media, advertisements, and other branding materials.
• Brand Recognition: Maintain our current logo and color scheme while exploring creative ways to establish a distinctive brand identity. The website should be a cornerstone for a cohesive branding strategy.
• Media Integration: Include images or videos on the website to enhance engagement. Find suitable, free-to-use visuals.
• Responsiveness: Ensure the design is responsive and works seamlessly on all devices.
• Demo Booking Form: Improve the design of the form to book a demo.
• Multilingual Support: Enable language transformation; the website is currently in Danish but should cater to other countries.

Guidelines:
• Typography: Up to the designer's discretion.
• Images/Videos: Must be free to use without additional charges.
• WordPress Theme: Use any WordPress theme below $100.
• Logo Redesign: Not needed; stick to the referenced color palette, as our new logo uses these colors.
• Color Palette: Stick to the existing company colors for consistency:
RGB
• #000b3c
• #004c6c
• #319ac3
• Greytones and white are also allowed
• Creativity Encouraged: Embrace creativity within the color palette for the layout, visuals, and overall user experience.

Conclusion: The Paperlynx website redesign marks an exciting opportunity to enhance our online presence. Our goal is to achieve a balance between a modern, attractive design and a clear, informative representation of our innovative solutions. We envision the revamped website as the foundation for a compelling online brand presence, with versatile graphic elements resonating across various digital platforms.

Sections that the website must include: Space for customer logos, space for testimonials, Space and redesign for display of price structure and price comparison, sections for company details and other information.

Design should also include a redesign of the customer cases section.
Generally there should just be a redesign of all things that are on the website.

Link to current website: https://paperlynx.example/

Target Market(s)

+50 employees.

Industry/Entity Type

Document automation

Coding

Coded - Design and coding required

Number of Pages Required

5+ page

Colors
0054AA
0677BA
7BADD7
CADEEF
E8F1F8

Requirements
Must have
• The new webpage must have the same pages as the current one. Frontpage, Book demo, About us, Case stories and Pricing

```html
<!DOCTYPE html>
<html lang="da">
<head>
<meta charset="utf-8">
<title>Om os – Paperlynx</title>
<link rel="stylesheet" href="https://fonts.googleapis.com/css2?family=Poppins:wght@300;400;500;600&family=Rubik:wght@500;600;700&family=Roboto:wght@700&family=Lato:wght@400&display=swap">
<style>
:root{
  --navy:#000b3c;
  --petrol:#004c6c;
  --heading:#065577;
  --sky:#319ac3;
  --accent:#0a9ad6;
  --accent-bright:#1aa3e8;
  --tint:#f0fcfd;
  --text:#7a7f86;
  --ink:#1c1f2b;
  --line:#d5e6ef;
  --footer:#02203c;
  --white:#ffffff;
}
*{margin:0;padding:0;box-sizing:border-box}
html,body{width:1200px;height:4231px;overflow:hidden}
body{position:relative;background:var(--white);font-family:"Poppins",sans-serif;color:var(--text)}
.abs{position:absolute}

/* header */
.hero-band{left:0;top:0;width:1200px;height:522px;background:var(--tint);border-top:2px solid #222}
.brand{left:66px;top:28px;display:flex;align-items:center;gap:10px;font-family:"Poppins",sans-serif;font-weight:600;font-size:22px;color:var(--petrol);letter-spacing:.5px}
.brand-mark{width:30px;height:30px;background:var(--petrol)}
.nav{left:410px;top:36px;display:flex;gap:28px;font-size:16px;font-weight:500;color:var(--ink)}
.nav .active{color:#7cbd1e}
.btn-demo{left:985px;top:31px;width:141px;height:32px;background:var(--accent);color:#fff;font-size:13.5px;font-weight:500;display:flex;align-items:center;justify-content:center;border-radius:2px}
.page-title{left:0;width:1200px;top:162px;text-align:center;font-family:"Rubik",sans-serif;font-weight:700;font-size:52px;color:var(--heading)}

.feature{top:356px;width:340px;display:flex;gap:22px}
.feature-icon{flex:none;width:52px;height:52px;border-radius:50%;background:var(--accent);margin-top:18px;display:flex;align-items:center;justify-content:center}
.feature h3{font-weight:500;font-size:15.5px;letter-spacing:1px;color:var(--ink);margin-bottom:6px}
.feature p{font-size:11.5px;line-height:19px;font-weight:300}

/* history */
.section-title{left:0;width:1200px;text-align:center;font-family:"Roboto",sans-serif;font-weight:700;font-size:41px;color:var(--heading)}
.prose{font-size:12px;line-height:29px;font-weight:300;color:var(--text)}
.prose b{font-weight:600;color:#4b4f57}
.prose a{color:var(--ink);font-weight:500;text-decoration:underline}
.prose p+p{margin-top:29px}
.illustration{border-radius:36px;background:linear-gradient(135deg,#e4f5fc 0%,#9fd6ee 40%,#2aa6db 75%,#0a8cc6 100%)}

/* timeline */
.timeline-band{left:0;top:1934px;width:1200px;height:1234px;background:var(--tint)}
.timeline-rail{left:598px;top:2047px;width:3px;height:921px;background:var(--line)}
.timeline-progress{left:598px;top:2047px;width:3px;height:50px;background:var(--accent)}
.dot{width:14px;height:14px;border-radius:50%;border:2px solid var(--accent);background:var(--tint);left:593px}
.year{font-size:15px;font-weight:500;color:var(--ink)}
.card{background:#fff;box-shadow:0 4px 18px rgba(10,60,90,.09);padding:26px 24px}
.card h4{font-family:"Poppins",sans-serif;font-weight:400;font-size:20px;color:var(--ink);margin:16px 0 10px}
.card p{font-family:"Lato",sans-serif;font-size:13.5px;line-height:29px;color:#6e7279}
.card.left{text-align:right}
.card svg{display:inline-block}

/* team */
.member{top:3324px;width:335px;height:481px;background:#fff;box-shadow:0 6px 24px rgba(10,60,90,.10);text-align:center;padding-top:33px}
.portrait{width:148px;height:148px;border-radius:50%;margin:0 auto;background:linear-gradient(160deg,#c8ced4 0%,#8d969e 55%,#dfe3e6 100%)}
.member h5{font-family:"Rubik",sans-serif;font-weight:600;font-size:19px;color:var(--sky);margin-top:54px}
.member .role{font-size:11px;color:#9aa0a6;margin-top:6px}
.member .bio{font-size:10.5px;line-height:15px;color:#8a8f95;padding:0 22px;margin-top:16px;height:78px}
.socials{display:flex;justify-content:center;gap:14px;margin-top:18px}
.socials span{width:27px;height:27px;border-radius:50%;background:var(--accent)}

/* footer */
.footer{left:0;top:3891px;width:1200px;height:303px;background:var(--footer);color:#fff}
.footer-brand{left:75px;top:3972px;display:flex;align-items:center;gap:8px;font-size:13px;font-weight:500;color:var(--accent-bright)}
.footer-brand i{width:20px;height:20px;background:var(--accent-bright);display:block}
.tagline{left:75px;top:4020px;width:300px;font-size:16px;line-height:28px;color:#fff}
.foot-socials{left:75px;top:4098px;display:flex;gap:22px}
.foot-socials span{width:18px;height:18px;border-radius:50%;background:var(--accent-bright)}
.foot-head{font-size:14.5px;font-weight:500;color:var(--accent-bright)}
.foot-list{list-style:none;font-size:13.5px;font-weight:500;color:#fff}
.foot-list li{display:flex;align-items:center;gap:10px;height:34px}
.copyright{left:0;top:4194px;width:1200px;height:37px;background:var(--accent-bright);color:#fff;font-size:13px;display:flex;align-items:center;justify-content:center}
</style>
</head>
<body>

<div class="abs hero-band"></div>
<div class="abs brand"><span class="brand-mark"></span>PAPERLYNX</div>
<nav class="abs nav"><span>Forside</span><span>Kundecases</span><span>Video</span><span>Live Demo</span><span>Priser</span><span class="active">Om os</span></nav>
<div class="abs btn-demo">BOOK DEMO</div>
<h1 class="abs page-title">Om Os</h1>

<div class="abs feature" style="left:74px">
  <div class="feature-icon"><svg width="24" height="24" viewBox="0 0 24 24" fill="none" stroke="#fff" stroke-width="1.8"><rect x="3" y="4" width="18" height="12" rx="1"/><path d="M8 20h8M12 16v4"/></svg></div>
  <div><h3>AVANCERET SOFTWARE</h3><p>Vi tror på, at fleksibelt software kan ændre måden kontrakter oprettes på, så de kan oprettes hurtigt og fejlfrit.</p></div>
</div>
<div class="abs feature" style="left:430px">
  <div class="feature-icon"><svg width="22" height="22" viewBox="0 0 24 24" fill="none" stroke="#fff" stroke-width="1.8"><rect x="4" y="4" width="16" height="16" rx="1"/><path d="M8 9h8M8 13h8M8 17h5"/></svg></div>
  <div><h3>TILGÆNGELIGHED</h3><p>Vi tror på, at vores service kan bygges intuitivt, så alle uanset erfaring kan danne kontrakter i høj ensartet kvalitet – du bliver din egen jurist.</p></div>
</div>
<div class="abs feature" style="left:787px;top:347px">
  <div class="feature-icon"><svg width="24" height="24" viewBox="0 0 24 24" fill="none" stroke="#fff" stroke-width="1.8"><path d="M5 19C5 10 11 5 20 5c0 9-6 14-15 14zM5 19l8-8"/></svg></div>
  <div><h3>GRØNT AFTRYK</h3><p>Vi tror på, at verden kan gøres grønnere ved effektivt at automatisere oprettelsen af kontrakter, så behovet for at printe helt forsvinder.</p></div>
</div>

<h2 class="abs section-title" style="top:572px">HISTORIE</h2>
<div class="abs prose" style="left:74px;top:776px;width:510px">
  <p>Paperlynx startede med et ønske om at gøre det let og billigt at oprette juridiske dokumenter. Det var vanskeligt at sammenligne priser, og de eksisterende skabeloner var svære at udfylde. Paperlynx' stifter <a>Jonas Vestergaard</a> prøvede den besværlige proces på egen hånd, og så en mulighed i at gøre den strømlinet og digital.</p>
  <p>Sammen med en partner udviklede Jonas en <b>intelligent dokumentløsning</b>, der skulle <b>bygge bro mellem advokaten og klienten</b>. Løsningen blev tilbudt til advokater som en White label løsning, hvor advokaten selv kunne vælge, hvilke dokumenter, klienten skulle kunne oprette, og det blev hurtigt populært.</p>
</div>
<div class="abs illustration" role="img" aria-label="Illustration: en person ved siden af en stor klemmemappe med et underskrevet samtykkedokument" style="left:612px;top:706px;width:480px;height:476px"></div>

<div class="abs illustration" role="img" aria-label="Illustration: en person der afkrydser punkter på en tjekliste i en klemmemappe" style="left:79px;top:1313px;width:479px;height:493px;background:linear-gradient(225deg,#e4f5fc 0%,#9fd6ee 40%,#2aa6db 75%,#0a8cc6 100%)"></div>
<div class="abs prose" style="left:609px;top:1424px;width:520px">
  <p>For at advokaten blev mere effektiv med det samme, var det vigtigt, at der fulgte opdateret indhold med en White label løsning. Derfor indgik vi et strategisk samarbejde med <b>Vellum Docs</b>, der via et redaktørnetværk automatiserede en stor dokumentsamling i vores løsning. Dokumentsamlingen opdateres ved lovændringer og sikrer, at den enkelte advokat ikke skal tænke på at automatisere sine egne dokumenter eller bekymre sig om lovændringer.</p>
  <p>Vi har løbende oplevet efterspørgsel på automatisering af tilbud og kundekontrakter, imens vi har været fokuserede på advokatbranchen. Derfor har vi nu lanceret en SaaS løsning i Paperlynx' eget brand, hvor alle typer af tilbud og kundekontrakter kan oprettes hurtigt og fejlfrit.</p>
</div>

<div class="abs timeline-band"></div>
<div class="abs timeline-rail"></div>
<div class="abs timeline-progress"></div>

<div class="abs dot" style="top:2040px"></div>
<div class="abs year" style="left:641px;top:2036px">2017</div>
<div class="abs card left" style="left:85px;top:1978px;width:476px;height:210px">
  <svg width="28" height="28" viewBox="0 0 24 24" fill="none" stroke="#31a8d8" stroke-width="1.4"><path d="M9 17h6M10 20h4M12 3a6 6 0 0 0-3.5 10.9V16h7v-2.1A6 6 0 0 0 12 3z"/></svg>
  <h4>Idé</h4>
  <p>Efter at have oplevet hvor besværligt og dyrt det var at oprette et juridisk dokument, så vi en mulighed i at gøre hele processen digital.</p>
</div>

<div class="abs dot" style="top:2321px"></div>
<div class="abs year" style="left:524px;top:2317px">2018</div>
<div class="abs card" style="left:637px;top:2251px;width:478px;height:238px">
  <svg width="30" height="28" viewBox="0 0 24 24" fill="none" stroke="#31a8d8" stroke-width="1.4"><path d="M4 9h4l5-4v14l-5-4H4zM16 9a4 4 0 0 1 0 6M18.5 6.5a8 8 0 0 1 0 11"/></svg>
  <h4>Første advokat løsninger</h4>
  <p>Vi oplevede stor interesse for vores løsning til en advokat konference, og det resulterede hurtigt i den første ud af mange White label portaler.</p>
</div>

<div class="abs dot" style="top:2631px"></div>
<div class="abs year" style="left:641px;top:2627px">2020</div>
<div class="abs card left" style="left:85px;top:2551px;width:476px;height:268px">
  <svg width="26" height="30" viewBox="0 0 24 24" fill="none" stroke="#31a8d8" stroke-width="1.4"><rect x="5" y="3" width="14" height="18" rx="1"/><path d="M8 8h8M8 12h8M8 16h5"/></svg>
  <h4>Strategisk samarbejde</h4>
  <p>Ved at indgå et strategisk samarbejde med Vellum Docs, kunne vi lancere en SaaS løsning målrettet advokat og revisionsbranchen. Nu kan alle advokatvirksomheder danne juridiske dokumenter med deres eget brand, uden at skulle have deres egen White label portal.</p>
</div>

<div class="abs dot" style="top:2961px"></div>
<div class="abs year" style="left:524px;top:2957px">2021</div>
<div class="abs card" style="left:637px;top:2881px;width:478px;height:268px">
  <div style="text-align:right"><svg width="32" height="28" viewBox="0 0 24 24" fill="none" stroke="#31a8d8" stroke-width="1.4"><path d="M2 12l4-4 4 2 4-2 4 2 4-2M6 8v6l4 4 4-2 4-2V10"/></svg></div>
  <h4 style="margin-top:8px">Ny investor</h4>
  <p>Nogen synes, at løsningen var så interessant, at de nærmest insisterede på at få lov til at købe sig ind i virksomheden. Dette øgede mulighederne for forretningen og sikrede at dygtige ressourcer til den fremadrettede vækst.</p>
</div>

<h2 class="abs section-title" style="top:3208px">LEDELSE</h2>

<div class="abs member" style="left:75px">
  <div class="portrait" role="img" aria-label="Portrætfoto af Jonas Vestergaard"></div>
  <h5>Jonas Vestergaard</h5>
  <div class="role">CEO · jv@paperlynx.example</div>
  <p class="bio">Ansvarlig for partnerskaber og softwareudvikling. Jonas har knap 20 års erfaring i IT-branchen, hvor han har været udvikler, projektleder og afdelingsleder. Han er uddannet IT-ingeniør og har speciale i softwareudvikling og teknologi.</p>
  <div class="socials"><span></span><span></span></div>
</div>
<div class="abs member" style="left:432px">
  <div class="portrait" role="img" aria-label="Portrætfoto af Kim Lykkegaard"></div>
  <h5>Kim Lykkegaard</h5>
  <div class="role">CSO · kl@paperlynx.example</div>
  <p class="bio">Ansvarlig for det kommercielle. Kim har over 25 års erhvervserfaring som konsulent, sælger, projektchef og salgsdirektør. Han er uddannet teolog og har altid fundet dialogen mellem mennesker fascinerende.</p>
  <div class="socials"><span></span><span></span></div>
</div>
<div class="abs member" style="left:788px">
  <div class="portrait" role="img" aria-label="Portrætfoto af Mikkel Holm Brandt"></div>
  <h5>Mikkel Holm Brandt</h5>
  <div class="role">Partner · mhb@paperlynx.example</div>
  <p class="bio">Ansvarlig for konsulentområdet samt økonomi. Mikkel har 10 års erfaring i IT-branchen som både udførende og rådgivende konsulent. Han er uddannet cand.it. med speciale i algoritmer og softwareudvikling.</p>
  <div class="socials"><span></span><span></span></div>
</div>

<div class="abs footer"></div>
<div class="abs footer-brand"><i></i>PAPERLYNX</div>
<p class="abs tagline">Opret fejlfrie kontrakter og tilbud hurtigt</p>
<div class="abs foot-socials"><span></span><span></span><span></span></div>

<div class="abs foot-head" style="left:432px;top:3973px">Features</div>
<ul class="abs foot-list" style="left:430px;top:4008px">
  <li><svg width="12" height="10" viewBox="0 0 12 10" fill="none" stroke="#1aa3e8" stroke-width="1.6"><path d="M0 5h10M6 1l4 4-4 4"/></svg>Få afsnit indsat automatisk</li>
  <li><svg width="12" height="10" viewBox="0 0 12 10" fill="none" stroke="#1aa3e8" stroke-width="1.6"><path d="M0 5h10M6 1l4 4-4 4"/></svg>Få priser beregnet automatisk</li>
  <li><svg width="12" height="10" viewBox="0 0 12 10" fill="none" stroke="#1aa3e8" stroke-width="1.6"><path d="M0 5h10M6 1l4 4-4 4"/></svg>Fjern manuelt arbejde</li>
  <li><svg width="12" height="10" viewBox="0 0 12 10" fill="none" stroke="#1aa3e8" stroke-width="1.6"><path d="M0 5h10M6 1l4 4-4 4"/></svg>Underskriv digitalt</li>
</ul>

<div class="abs foot-head" style="left:788px;top:3973px">KONTAKT</div>
<ul class="abs foot-list" style="left:788px;top:4008px">
  <li><svg width="16" height="13" viewBox="0 0 16 13" fill="none" stroke="#1aa3e8" stroke-width="1.5"><rect x="1" y="1" width="14" height="11" rx="1"/><path d="M1 2l7 5 7-5"/></svg>contact@paperlynx.example</li>
  <li style="margin-top:4px"><svg width="15" height="15" viewBox="0 0 24 24" fill="#1aa3e8"><path d="M6.6 10.8a15 15 0 0 0 6.6 6.6l2.2-2.2a1 1 0 0 1 1-.25 11.4 11.4 0 0 0 3.6.6 1 1 0 0 1 1 1V20a1 1 0 0 1-1 1A17 17 0 0 1 3 4a1 1 0 0 1 1-1h3.5a1 1 0 0 1 1 1c0 1.25.2 2.45.6 3.6a1 1 0 0 1-.25 1z"/></svg>+45 00 00 00 00</li>
  <li style="margin-top:4px"><svg width="13" height="17" viewBox="0 0 24 30" fill="#1aa3e8"><path d="M12 0a12 12 0 0 0-12 12c0 9 12 18 12 18s12-9 12-18A12 12 0 0 0 12 0zm0 16a4 4 0 1 1 0-8 4 4 0 0 1 0 8z"/></svg>Eksempelvej 12, 2700 Byhavn</li>
</ul>

<div class="abs copyright">Copyright © 2023.&nbsp; All Rights Reserved</div>

</body>
</html>
```